Modernize and improve usability of our webpage www.lernwandel.ch (4 languages, mostly static content)

Need to modernize and freshen up the webpages of our association: www.lernwandel.ch We offer apprenticeship exchanges within Switzerland and abroad. Young people can inform and enroll online. We do the matchmaking with work locations and organize logistics, stay overs etc.
The webpage needs to be in 4 languages (German, French, Italian and English). The main pages will be:
- Landing page: what we do, targeted to our apprentices / young people who enroll for the stages.
- Sup-Page: Registration form for interested apprentices to sign up for the program
- Sub-Page "Company", the firms who would like to send their apprentices on a internship and info on how to join the program
- Sub-Page "Host Family", private people who would be interested in hosting the apprentices (for free) during the stages. Find out about the reqiurements for the host families
- Sub-Page "About Us", who we are, executive team, board of director, our sponsor "Falkner Circle Switzerland"
- Footer: contact (E-Mail, Telephone, WhatsApp), Bank details (IBAN Number), Partnerlogo of Falkner-Circle (see uploaded jpg), Social-Media Links (Facebook, LinkedIn)

Target Market(s)

Young people looking for a "apprenticeship" stage within Switzerland or going from Switzerland abroad

Industry/Entity Type

Apprenticeships: cooks, builders, craftsman, office support, etc.

Number of Pages Required

5+ page

Font styles to use
Other font styles liked:
• Lato (sans serif)

Requirements
Must have
• use colors shown on uploaded PDF-Slides: Make the BLUE the MAIN color, the ORANGE as a secondary color
Nice to have
• Forms using e.g. google forms or survey-monkey forms (external links, no code). Matching & appealing visuals showing young apprentices (can use stock photos)

```html
<!DOCTYPE html>
<html lang="en">
<head>
<meta charset="utf-8">
<title>Lernwandel – Apprentice Exchange</title>
<link href="https://fonts.googleapis.com/css2?family=Lato:wght@400;700&family=Roboto:wght@400;500;700&display=swap" rel="stylesheet">
<style>
:root{
  --blue:#24528d;
  --blue-dark:#1d4578;
  --orange:#c9500f;
  --ink:#2b2b2b;
  --text:#6a6a6a;
  --nav:#6f6f6f;
  --footer:#232323;
  --white:#ffffff;
  --field:#f2f2f2;
}
*{box-sizing:border-box;margin:0;padding:0}
html,body{width:1200px;height:4357px;overflow:hidden}
body{position:relative;background:var(--white);font-family:"Lato",sans-serif;color:var(--text)}
.abs{position:absolute}

.btn{position:absolute;display:flex;align-items:center;justify-content:center;gap:10px;height:48px;border-radius:24px;color:var(--white);font:700 15px/1 "Lato",sans-serif;text-transform:uppercase;letter-spacing:.2px}
.btn--orange{background:var(--orange)}
.btn--blue{background:var(--blue)}
.arrow{width:13px;height:13px;border-radius:50%;background:var(--white);position:relative;flex:none}
.arrow::after{content:"";position:absolute;left:5px;top:3.5px;border-left:4px solid var(--orange);border-top:3px solid transparent;border-bottom:3px solid transparent}
.btn--blue .arrow::after{border-left-color:var(--blue)}
.heading{position:absolute;font:700 38px/1 "Lato",sans-serif;color:var(--ink)}
.rule{position:absolute;height:4px;width:52px;background:var(--orange)}
.photo{position:absolute}

.site-header{position:absolute;left:0;top:0;width:1200px;height:150px;background:var(--white)}
.brand{position:absolute;left:112px;top:62px;font:700 47px/1 "Lato",sans-serif;color:var(--orange);letter-spacing:-1px}
.social{position:absolute;display:flex;gap:8px}
.social span{width:42px;height:42px;border-radius:50%;background:var(--blue);color:var(--white);display:flex;align-items:center;justify-content:center;font:700 12px/1 "Lato",sans-serif}
.search{position:absolute;left:670px;top:28px;width:270px;height:44px;border-radius:22px;background:#f0f0f0;padding:0 20px;display:flex;align-items:center;justify-content:space-between;font-size:14px;color:#666}
.login{position:absolute;left:948px;top:28px;width:140px;height:44px;border-radius:22px;background:var(--orange);color:var(--white);font:700 15px/1 "Lato",sans-serif;display:flex;align-items:center;justify-content:center;gap:8px}
.main-nav{position:absolute;top:106px;left:0;font:400 15px/1 "Lato",sans-serif;color:var(--nav);text-transform:uppercase}
.main-nav span{position:absolute;white-space:nowrap}
.lang{position:absolute;left:1005px;top:101px;display:flex;align-items:center;gap:10px;font:700 15px/1 "Lato",sans-serif;color:#444}
.lang i{width:22px;height:22px;border-radius:50%;background:var(--blue);display:block}

.hero{position:absolute;left:0;top:150px;width:1200px;height:618px}
.hero-panel{position:absolute;left:87px;top:142px;width:470px;height:335px;background:rgba(20,24,30,.55)}
.hero-title{position:absolute;left:48px;top:40px;font:700 70px/1 "Lato",sans-serif;color:var(--white);letter-spacing:-1px}
.hero-text{position:absolute;left:48px;top:152px;width:400px;font:400 13.5px/26px "Lato",sans-serif;color:var(--white)}

.body-text{position:absolute;font:400 14.5px/27.5px "Lato",sans-serif;color:var(--text)}

.panel{position:absolute;top:1355px;width:600px;height:478px}
.panel--blue{left:0;background:var(--blue)}
.panel--orange{left:600px;background:var(--orange)}
.panel-icon{position:absolute;left:112px;top:65px;width:100px;height:100px;border-radius:50%;background:var(--white);display:flex;align-items:center;justify-content:center}
.panel-title{position:absolute;left:234px;top:102px;font:700 26px/1 "Lato",sans-serif;color:var(--white)}
.panel-text{position:absolute;left:112px;top:186px;width:422px;font:400 13.5px/26.6px "Lato",sans-serif;color:var(--white);text-align:justify}

.team-names{position:absolute;left:111px;top:2228px;width:440px;font:400 14.5px/27.5px "Lato",sans-serif;color:var(--orange)}
.about-ring{position:absolute;left:648px;top:1932px;width:432px;height:432px;border-radius:50%;border:4px solid var(--blue);border-left-color:var(--orange);border-bottom-color:var(--orange);padding:8px}
.about-ring .photo{position:static;width:100%;height:100%;border-radius:50%;background:linear-gradient(150deg,#8d8f92,#5d6a7b 55%,#2f3f6b)}

.accom{position:absolute;left:0;top:2458px;width:1200px;height:396px;background:linear-gradient(180deg,#c4520f,#cd5612)}
.accom .heading,.contact .heading{color:var(--white);width:1200px;text-align:center;left:0}
.accom-text{position:absolute;left:190px;top:142px;width:820px;text-align:center;font:400 14px/27px "Lato",sans-serif;color:var(--white)}

.card{position:absolute;top:2940px;width:464px;height:293px;border-radius:12px;border:3px solid var(--blue-dark);overflow:hidden}
.card .photo{position:static;width:100%;height:100%}
.card-name{position:absolute;top:3252px;width:464px;text-align:center;font:400 19px/1 "Lato",sans-serif;color:var(--ink)}
.card-link{position:absolute;top:3290px;width:464px;display:flex;justify-content:center;align-items:center;gap:10px;font:700 16px/1 "Lato",sans-serif;color:var(--blue)}
.card-link .arrow{background:var(--blue)}
.card-link .arrow::after{border-left-color:var(--white)}

.contact{position:absolute;left:0;top:3393px;width:1200px;height:525px;background:var(--blue)}
.field{position:absolute;left:160px;width:425px;height:56px;border-radius:28px;background:var(--field);padding:0 30px;display:flex;align-items:center;font:400 13px/1 "Lato",sans-serif;color:#999}
.field--message{left:611px;top:175px;width:430px;height:195px;border-radius:24px;align-items:flex-start;padding-top:30px}

.site-footer{position:absolute;left:0;top:3918px;width:1200px;height:439px;background:var(--footer)}
.f-head{position:absolute;font:700 20px/1 "Roboto",sans-serif;color:var(--white)}
.f-rule{position:absolute;height:2px;width:38px;background:var(--orange)}
.f-row{position:absolute;left:115px;display:flex;align-items:center;gap:18px;font:500 14px/1 "Roboto",sans-serif;color:var(--white)}
.f-row i{width:28px;height:28px;border-radius:50%;background:var(--white);display:flex;align-items:center;justify-content:center}
.f-row--big{font-size:17px}
.newsletter{position:absolute;left:483px;top:4118px;width:296px;height:42px;border-radius:21px;background:var(--white);display:flex;align-items:center;padding-left:16px;gap:8px;font:400 12px/1 "Roboto",sans-serif;color:#777}
.newsletter b{position:absolute;right:4px;top:4px;width:112px;height:34px;border-radius:17px;background:var(--orange);color:var(--white);font:700 11px/34px "Roboto",sans-serif;text-align:center;text-transform:uppercase}
.partner{position:absolute;left:923px;top:4122px;font:700 20px/1 "Roboto",sans-serif;color:var(--white)}
.f-nav{position:absolute;top:4270px;left:0;width:1200px;display:flex;justify-content:center;gap:37px;font:700 14.5px/1 "Roboto",sans-serif;color:var(--white)}
.copy{position:absolute;top:4314px;width:1200px;left:0;text-align:center;font:400 13px/1 "Roboto",sans-serif;color:var(--white)}
</style>
</head>
<body>

<header class="site-header">
  <div class="brand">lernwandel</div>
  <div class="social" style="left:518px;top:29px">
    <span>Fb</span><span>Li</span><span>Wa</span>
  </div>
  <div class="search">Search
    <svg width="14" height="14" viewBox="0 0 14 14"><circle cx="6" cy="6" r="4.5" fill="none" stroke="#444" stroke-width="2"/><line x1="9.5" y1="9.5" x2="13" y2="13" stroke="#444" stroke-width="2"/></svg>
  </div>
  <div class="login">LOGIN
    <svg width="10" height="12" viewBox="0 0 10 12"><rect x="0" y="5" width="10" height="7" rx="1" fill="#fff"/><path d="M2.5 5V3.5a2.5 2.5 0 0 1 5 0V5" fill="none" stroke="#fff" stroke-width="1.6"/></svg>
  </div>
  <nav class="main-nav">
    <span style="left:364px">Home</span>
    <span style="left:437px">About Us</span>
    <span style="left:536px">Registration</span>
    <span style="left:668px">Company</span>
    <span style="left:769px">Host Family</span>
    <span style="left:889px">Contact Us</span>
  </nav>
  <div class="lang"><i></i>ENG
    <svg width="10" height="7" viewBox="0 0 10 7"><path d="M1 1l4 4 4-4" fill="none" stroke="#444" stroke-width="1.6"/></svg>
  </div>
</header>

<section class="hero">
  <div class="photo" role="img" aria-label="Smiling apprentice in a white work shirt at a workplace desk" style="left:0;top:0;width:1200px;height:618px;background:linear-gradient(100deg,#3b4046 0%,#4c5257 35%,#6d6e6c 55%,#3a3f3c 80%,#24302a 100%)"></div>
  <div class="hero-panel">
    <h1 class="hero-title">Lernwandel</h1>
    <p class="hero-text">Lernwandel has been organizing the exchange of apprentices between different cultural and language regions within Switzerland as well as with other countries for more than 19 years.</p>
    <a class="btn btn--orange" style="left:48px;top:256px;width:177px">Get Started <span class="arrow"></span></a>
  </div>
</section>

<section class="what-we-do">
  <div class="photo" role="img" aria-label="Apprentice florist among flowers" style="left:112px;top:855px;width:201px;height:335px;background:linear-gradient(160deg,#6b6a3c,#9a7a5c 45%,#4e6b2c)"></div>
  <div class="photo" role="img" aria-label="Apprentice in high-visibility jacket taking notes" style="left:323px;top:860px;width:254px;height:250px;background:linear-gradient(150deg,#5d6367,#a7c24b 55%,#dfe2e4)"></div>
  <svg class="abs" style="left:408px;top:1110px" width="72" height="106"><path d="M70 0V103H4" fill="none" stroke="#24528d" stroke-width="3"/></svg>
  <div class="photo" role="img" aria-label="Apprentice cooks plating food in a kitchen" style="left:188px;top:1060px;width:220px;height:205px;background:linear-gradient(160deg,#c9c3bb,#7c5a4a 45%,#a3b46a);border:4px solid #fff"></div>
  <h2 class="heading" style="left:666px;top:870px">What We Do</h2>
  <div class="rule" style="left:666px;top:920px"></div>
  <p class="body-text" style="left:666px;top:936px;width:424px">Lorem ipsum dolor sit amet, consectetur adipiscing elit, sed do eiusmod tempor incididunt ut labore et dolore magna aliqua. Ut enim ad minim veniam, quis nostrud exercitation ullamco laboris nisi ut aliquip ex ea commodo consequat. Duis aute irure dolor in reprehenderit in voluptate velit esse cillum dolore eu fugiat nulla pariatur. Excepteur sint occaecat cupidatat non proident, sunt in culpa qui officia deserunt mollit anim id est laborum.</p>
  <p class="body-text" style="left:666px;top:1131px;width:424px">perspiciatis unde omnis&nbsp; natus error&nbsp; voluptatem accusantium doloremque laudantium, totam rem aperiam eaque ipsad.</p>
  <a class="btn btn--orange" style="left:666px;top:1202px;width:177px">Learn More <span class="arrow"></span></a>
</section>

<section class="panel panel--blue">
  <div class="panel-icon">
    <svg width="48" height="60" viewBox="0 0 48 60"><circle cx="24" cy="14" r="12" fill="#c9500f"/><text x="24" y="19" text-anchor="middle" font-family="Lato,sans-serif" font-weight="700" font-size="15" fill="#fff">$</text><path d="M24 26v14M24 36c-6-8-14-6-14-6s2 8 14 8M24 34c6-8 14-6 14-6s-2 8-14 8" fill="#c9500f" stroke="#c9500f" stroke-width="2"/><path d="M12 42h24l-4 16H16z" fill="#c9500f"/></svg>
  </div>
  <h3 class="panel-title">Profit</h3>
  <p class="panel-text">By taking part in this exchange programme, you broaden your professional as well as your personal horizon. Not only do you get to know a new environment, the challenge will be for you to adapt to it and demonstrating your high level of flexibility. You meet new people both at home and abroad and make new contacts, which are often maintained even after the exchange is over.</p>
  <a class="btn btn--orange" style="left:112px;top:363px;width:178px">Learn More <span class="arrow"></span></a>
</section>

<section class="panel panel--orange">
  <div class="panel-icon" style="left:88px">
    <svg width="60" height="56" viewBox="0 0 60 56"><ellipse cx="40" cy="10" rx="12" ry="4" fill="#24528d"/><rect x="28" y="10" width="24" height="18" fill="#24528d"/><circle cx="34" cy="24" r="9" fill="#fff" stroke="#24528d" stroke-width="2.5"/><text x="34" y="29" text-anchor="middle" font-family="Lato,sans-serif" font-weight="700" font-size="12" fill="#24528d">$</text><path d="M14 4v16M9 9l5-5 5 5" fill="none" stroke="#24528d" stroke-width="2.5"/><path d="M4 44c8-8 16-8 24-4h12c3 0 3 4 0 4H28M4 52c10-4 24 2 34-4l14-10c3-2 5 1 3 3L40 54" fill="none" stroke="#24528d" stroke-width="2.5"/></svg>
  </div>
  <h3 class="panel-title" style="left:210px">Costs</h3>
  <p class="panel-text" style="left:88px">Your training company continues paying your normal wage during the exchange. Whenever possible you live with a host family, where you have breakfast and dinner. Lernwandel or the local Falkner-Circle will provide financial support for any expenses arising from the accommodation. Only travel costs, lunch and any leisure activities need to be paid by yourself. The mediation and organisation</p>
  <a class="btn btn--blue" style="left:88px;top:363px;width:178px">Learn More <span class="arrow"></span></a>
</section>

<section class="about">
  <h2 class="heading" style="left:111px;top:1917px">About Us</h2>
  <div class="rule" style="left:111px;top:1965px"></div>
  <p class="body-text" style="left:111px;top:1982px;width:472px;text-align:justify">Lernwandel has been organizing the exchange of apprentices between different cultural and language regions within Switzerland as well as with other countries for more than 19 years. Primary participants are all apprentices who are completing their basic vocational education and training. Once registered for the exchange, lernwandel will find a suitable exchange company and an appropriate accommodation, where the apprentice will go through an exchange of at least three weeks. Falkner Circle Switzerland/Liechtenstein mainly supports this program with the objective of promoting the mobility of apprentices.</p>
  <p class="team-names">Your lernwandel team<br>Selina Marti, Nadja Hürlimann, Chiara Bernasconi, Luca Ferretti und Mireille Dubois</p>
  <a class="btn btn--blue" style="left:111px;top:2325px;width:177px">Learn More <span class="arrow"></span></a>
  <div class="about-ring"><div class="photo" role="img" aria-label="Smiling apprentice in a blue sweatshirt in a workshop"></div></div>
</section>

<section class="accom">
  <h2 class="heading" style="top:70px">Offer An Accommodation</h2>
  <div class="rule" style="left:574px;top:120px;background:var(--white)"></div>
  <p class="accom-text">Finding a suitable accommodation is vital for a successful exchange. Whenever possible, the apprentices stay with host families where they can participate in family life. If placement in a host family is not possible, lernwandel finds another appropriate accommodation. Are you interested in hosting an apprentice? Feel free to contact our programme manager Lea Brunner for more information and registration as a future host family.</p>
  <a class="btn btn--blue" style="left:511px;top:276px;width:177px">Apply Now <span class="arrow"></span></a>
</section>

<section class="people">
  <div class="card" style="left:120px"><div class="photo" role="img" aria-label="Sales employee working at a computer with two monitors" style="background:linear-gradient(120deg,#e6e9ec,#9aa3ad 45%,#3d4a5c)"></div></div>
  <p class="card-name" style="left:120px">Sales Employee</p>
  <a class="card-link" style="left:120px">Read More <span class="arrow"></span></a>
  <div class="card" style="left:616px"><div class="photo" role="img" aria-label="Business woman on the phone at an office desk" style="background:linear-gradient(120deg,#3a3633,#6b5d52 40%,#e9e6e2)"></div></div>
  <p class="card-name" style="left:616px">Livia Business woman</p>
  <a class="card-link" style="left:616px">Read More <span class="arrow"></span></a>
</section>

<section class="contact">
  <h2 class="heading" style="top:82px">Contact Us</h2>
  <div class="rule" style="left:574px;top:130px;background:var(--white)"></div>
  <div class="field" style="top:177px">Name</div>
  <div class="field" style="top:247px">Phone Number</div>
  <div class="field" style="top:315px">Email Address</div>
  <div class="field" style="top:385px">Types of programs</div>
  <div class="field field--message">Message</div>
  <a class="btn btn--orange" style="left:611px;top:389px;width:193px;height:56px;border-radius:28px;font-size:16px">Submit Now <span class="arrow"></span></a>
</section>

<footer class="site-footer"></footer>
<div class="f-head" style="left:115px;top:4004px">Address</div>
<div class="f-rule" style="left:115px;top:4038px"></div>
<div class="f-row" style="top:4064px"><i><svg width="12" height="14" viewBox="0 0 12 14"><path d="M6 14S1 8 1 5a5 5 0 0 1 10 0c0 3-5 9-5 9z" fill="#24528d"/><circle cx="6" cy="5" r="2" fill="#fff"/></svg></i>Lindenweg 24, 8600 Talwil</div>
<div class="f-row f-row--big" style="top:4124px"><i><svg width="14" height="14" viewBox="0 0 14 14"><path d="M3 1l3 3-2 2c1 2 2 3 4 4l2-2 3 3-2 2C6 13 1 8 1 3z" fill="#24528d"/></svg></i>+41 (0) 44 555 01 23</div>
<div class="f-row" style="top:4182px"><i><svg width="14" height="10" viewBox="0 0 14 10"><rect width="14" height="10" rx="1" fill="#24528d"/><path d="M1 1l6 5 6-5" fill="none" stroke="#fff" stroke-width="1.3"/></svg></i>info@lernwandel.ch</div>

<div class="f-head" style="left:481px;top:4004px">Subscribe Newsletter</div>
<div class="f-rule" style="left:481px;top:4038px"></div>
<p class="abs" style="left:481px;top:4056px;width:290px;font:400 13px/20px Roboto,sans-serif;color:#fff">Lorem ipsum dolor sit amet, consectetur adipiscing elit, sed do eiusmod</p>
<div class="newsletter"><svg width="12" height="9" viewBox="0 0 12 9"><rect width="12" height="9" rx="1" fill="#555"/><path d="M1 1l5 4 5-4" fill="none" stroke="#fff" stroke-width="1.2"/></svg>Email Address *<b>Subscribe</b></div>

<div class="f-head" style="left:923px;top:4004px">Follow Us On</div>
<div class="f-rule" style="left:923px;top:4038px"></div>
<div class="social" style="left:923px;top:4060px;gap:7px">
  <span style="width:32px;height:32px;font-size:10px">Fb</span><span style="width:32px;height:32px;font-size:10px">Li</span><span style="width:32px;height:32px;font-size:10px">Wa</span>
</div>
<div class="partner">Falkner Circle</div>

<div class="abs" style="left:111px;top:4245px;width:977px;height:1px;background:#4a4a4a"></div>
<nav class="f-nav">
  <span>Home</span><span>About Us</span><span>Registration</span><span>Company</span><span>Host Family</span><span>Contact Us</span>
</nav>
<p class="copy">© 2023&nbsp; Lernwandel.&nbsp; All Rights Reserved</p>

</body>
</html>
```